New Business Card Design for Manufacturing

We are an engineering/manufacturing company that offers Advanced machining/assembly/engineering services, as well as innovative products for the heavy duty engine cooling markets.

We are looking to get a new business card designed that is clean and modern looking, but still fits the wide range of technical/skilled work we do.

- We hope to use this design as the base for other design work in new Presentations, web, and print work.

Industry/Entity Type

Engineering

Contact Information for Business Card

Our preferred color of blue is (RGB) 22/71/159 but can vary slightly from that color. Our content will be our Logo and full company name (Vantrell Forge Works, Inc.), company address, name, job title, phone number with extension, cell number, fax number, website, and email address on the cards.
We'd like the full company name next to the logo, but we are open to other interpretations of that layout.
Preferably, we would like the back side to be clean with just our logo, and the front to contain all of the contact information.

Colors
2f74b4
0355a3
85abd2

Requirements
Must have
• - Logo, company name, needed content - We are open to interpretation beyond that.
• - Standard size business card.
• - Horizontal orientation.
• - Enough space for lengthy names / job titles (for example, a job title could read "Directory of Human Resources" or "V.P. of Governmental Affairs"). We need this to look clean, whether the title be short (CEO) or long (as described above).

```html
<!DOCTYPE html>
<html lang="en">
<head>
<meta charset="utf-8">
<title>Vantrell Forge Works – Business Card</title>
<link href="https://fonts.googleapis.com/css2?family=Open+Sans:wght@400;600;700&display=swap" rel="stylesheet">
<style>
  :root{
    --backdrop:#3b3b3d;
    --card:#1d1d1f;
    --gloss:#3c3c40;
    --brand-blue:#0f62c0;
    --rule-blue:#1f74d0;
    --ink:#f2f2f2;
    --icon:#cfd3d9;
  }
  *{margin:0;padding:0;box-sizing:border-box;}
  html,body{width:799px;height:1200px;overflow:hidden;}
  body{background:var(--backdrop);font-family:"Open Sans",Arial,sans-serif;position:relative;}
  .card{position:absolute;left:80px;width:640px;height:366px;background:var(--card);
        box-shadow:0 18px 40px rgba(0,0,0,.45);}
  .card--back{top:90px;}
  .card--front{top:700px;}

  .back-mark{position:absolute;left:0;right:0;top:138px;text-align:center;
             font-weight:700;font-size:78px;letter-spacing:2px;color:var(--gloss);}

  .front-mark{position:absolute;left:300px;top:40px;font-weight:700;font-size:52px;
              color:var(--brand-blue);letter-spacing:1px;}

  .person{position:absolute;right:340px;top:150px;text-align:right;color:var(--ink);}
  .person__name{font-size:23px;color:var(--brand-blue);font-weight:400;line-height:1.2;}
  .person__title{font-size:14px;margin-top:2px;}
  .person__address{font-size:14px;margin-top:8px;line-height:1.35;}

  .divider{position:absolute;left:318px;top:215px;width:1.5px;height:88px;background:var(--rule-blue);}
  .rule{position:absolute;left:40px;right:40px;top:318px;height:1.5px;background:var(--rule-blue);}

  .contacts{position:absolute;left:338px;top:204px;list-style:none;color:var(--ink);font-size:14.5px;}
  .contacts li{display:flex;align-items:center;height:20px;}
  .contacts svg{width:12px;height:12px;margin-right:12px;fill:var(--icon);flex:none;}
  .contacts .accent{color:var(--brand-blue);}

  .company{position:absolute;left:60px;top:328px;font-weight:700;font-size:16px;color:var(--ink);}
</style>
</head>
<body>
  <section class="card card--back" aria-label="Card back">
    <div class="back-mark">Vantrell</div>
  </section>

  <section class="card card--front" aria-label="Card front">
    <div class="front-mark">Vantrell</div>

    <div class="person">
      <div class="person__name">Marcus Hale Draper</div>
      <div class="person__title">Managing Director</div>
      <div class="person__address">58 Millrace Rd., Corbin Falls,<br>Ohio, US 44120</div>
    </div>

    <div class="divider"></div>

    <ul class="contacts">
      <li><svg viewBox="0 0 12 12"><path d="M2 1h3l1 3-1.5 1a6 6 0 0 0 2.5 2.5L8 6l3 1v3a1 1 0 0 1-1 1A9 9 0 0 1 1 2a1 1 0 0 1 1-1z"/></svg>216-555-0148 (VFW)</li>
      <li><svg viewBox="0 0 12 12"><path d="M3 0h6a1 1 0 0 1 1 1v10a1 1 0 0 1-1 1H3a1 1 0 0 1-1-1V1a1 1 0 0 1 1-1zm0 2v7h6V2z"/></svg>216-555-0193</li>
      <li><svg viewBox="0 0 12 12"><path d="M3 0h6v3H3zM1 4h10v5H9v3H3V9H1zm3 4v3h4V8z"/></svg>216-555-0176</li>
      <li><svg viewBox="0 0 12 12"><path d="M0 2h12v8H0zm1 1v.5L6 7l5-3.5V3z"/></svg>www.<span class="accent">vantrellforge</span>.com</li>
      <li><svg viewBox="0 0 12 12"><path d="M6 0a6 6 0 1 0 0 12A6 6 0 0 0 6 0zm0 1.2c.8 1 1.2 2.5 1.3 4.2H4.7C4.8 3.7 5.2 2.2 6 1.2zM1.3 6.6h2.2c.1 1.6.5 3 1.1 4A4.8 4.8 0 0 1 1.3 6.6zm0-1.2a4.8 4.8 0 0 1 3.3-4c-.6 1-1 2.4-1.1 4zm3.4 1.2h2.6C7.2 8.3 6.8 9.8 6 10.8c-.8-1-1.2-2.5-1.3-4.2zm3.8 0h2.2a4.8 4.8 0 0 1-3.3 4c.6-1 1-2.4 1.1-4zm0-1.2c-.1-1.6-.5-3-1.1-4a4.8 4.8 0 0 1 3.3 4z"/></svg>mdraper@vantrellforge.com</li>
    </ul>

    <div class="rule"></div>
    <div class="company">Vantrell Forge Works, Inc.</div>
  </section>
</body>
</html>
```